Book cover design for "The Ashward", supernatural thriller, (sub)urban fantasy genres

I need a full book cover design for my new novel, "The Ashward", Subtitle: "Book 1: Marcus" a story whose heart is about friendships, family, and small towns wrapped in the skin of a supernatural thriller and (sub)urban fantasy. I would like to see designs using those genre elements and colors but also carrying elements of fear and danger. The book would also fall somewhere into into YA and NA categories. I came up with a simple starting point and some other covers conveying some of the elements I like. They are attached.

```html
<!DOCTYPE html>
<html lang="en">
<head>
<meta charset="utf-8">
<title>The Ashward – Full Cover</title>
<link href="https://fonts.googleapis.com/css2?family=Orbitron:wght@800;900&family=Barlow+Condensed:wght@400&family=Saira+Condensed:wght@400&family=Cormorant+Garamond:wght@500&display=swap" rel="stylesheet">
<style>
  :root {
    --ink-deep: #04070c;
    --ink-navy: #0b1824;
    --mist-steel: #3f6a82;
    --mist-pale: #b3dbe9;
    --glow-core: #a2dcee;
    --figure-cyan: #12a9cc;
    --figure-deep: #0a6f8c;
    --title-white: #f4f5f7;
    --title-shade: #c9ced4;
    --text-white: #ffffff;
    --barcode-box: #ffffff;
  }
  * { margin: 0; padding: 0; box-sizing: border-box; }
  html, body {
    width: 1200px; height: 880px; overflow: hidden;
    background: var(--ink-deep);
  }
  .cover { position: relative; width: 1200px; height: 880px; overflow: hidden; }
  .dust-backdrop {
    position: absolute; inset: 0;
    background:
      radial-gradient(ellipse 250px 250px at 900px 360px, var(--glow-core) 0%, rgba(162,220,238,0.85) 35%, rgba(120,185,210,0) 100%),
      radial-gradient(ellipse 460px 380px at 880px 330px, rgba(120,180,205,0.85) 0%, rgba(70,125,155,0.45) 55%, rgba(10,20,30,0) 100%),
      radial-gradient(ellipse 260px 520px at 640px 260px, rgba(95,150,180,0.7) 0%, rgba(40,75,100,0) 100%),
      radial-gradient(ellipse 230px 320px at 470px 520px, rgba(70,115,150,0.65) 0%, rgba(20,40,60,0) 100%),
      radial-gradient(ellipse 340px 170px at 120px 60px, rgba(170,210,225,0.85) 0%, rgba(80,125,150,0.35) 50%, rgba(60,100,130,0) 100%),
      radial-gradient(ellipse 380px 150px at 380px 30px, rgba(120,170,195,0.55) 0%, rgba(60,100,130,0) 100%),
      radial-gradient(ellipse 360px 140px at 180px 830px, rgba(160,200,215,0.7) 0%, rgba(70,110,135,0) 100%),
      radial-gradient(ellipse 280px 120px at 660px 860px, rgba(100,140,160,0.45) 0%, rgba(60,100,130,0) 100%),
      radial-gradient(ellipse 220px 240px at 1180px 70px, rgba(4,7,12,1) 0%, rgba(4,7,12,0) 100%),
      radial-gradient(ellipse 360px 200px at 1150px 850px, rgba(4,7,12,1) 0%, rgba(4,7,12,0) 100%),
      radial-gradient(ellipse 200px 300px at 20px 420px, rgba(4,7,12,0.9) 0%, rgba(4,7,12,0) 100%),
      linear-gradient(180deg, var(--ink-navy) 0%, #0a1520 55%, var(--ink-deep) 100%);
  }
  .dust-grain { position: absolute; inset: 0; opacity: 0.55; mix-blend-mode: screen; }
  .figures-art {
    position: absolute; left: 784px; top: 370px; width: 256px; height: 240px;
    background: radial-gradient(ellipse 50% 50% at 50% 45%, var(--figure-cyan) 0%, rgba(18,169,204,0.85) 45%, rgba(10,111,140,0.35) 75%, rgba(10,111,140,0) 100%);
  }
  .svg-layer { position: absolute; inset: 0; }
  .title-text { font-family: "Orbitron", sans-serif; font-weight: 900; fill: url(#titleFill); }
  .blurb-line { font-family: "Barlow Condensed", sans-serif; font-size: 19px; fill: var(--text-white); text-anchor: middle; }
  .subtitle-text { font-family: "Saira Condensed", sans-serif; font-size: 38px; fill: var(--text-white); }
  .author-text { font-family: "Cormorant Garamond", serif; font-weight: 500; fill: var(--text-white); }
  .spine-title { font-family: "Orbitron", sans-serif; font-weight: 800; fill: var(--title-white); }
  .barcode-area {
    position: absolute; left: 342px; top: 721px; width: 197px; height: 122px;
    background: var(--barcode-box);
  }
</style>
</head>
<body>
<div class="cover">
  <div class="dust-backdrop" role="img" aria-label="Exploding blue dust cloud on a dark background, glowing brightest behind the front-cover figures"></div>

  <svg class="dust-grain" width="1200" height="880" viewBox="0 0 1200 880" aria-hidden="true">
    <defs>
      <filter id="speckle" x="0" y="0" width="100%" height="100%">
        <feTurbulence type="fractalNoise" baseFrequency="0.85" numOctaves="2" seed="7"/>
        <feColorMatrix values="0 0 0 0 0.72  0 0 0 0 0.86  0 0 0 0 0.96  0 0 0 10 -6"/>
      </filter>
    </defs>
    <rect width="1200" height="880" filter="url(#speckle)"/>
  </svg>

  <div class="figures-art" role="img" aria-label="Cyan silhouettes of four people walking toward the viewer out of the glow"></div>

  <svg class="svg-layer" width="1200" height="880" viewBox="0 0 1200 880">
    <defs>
      <linearGradient id="titleFill" x1="0" y1="0" x2="0" y2="1">
        <stop offset="0" stop-color="#ffffff"/>
        <stop offset="0.6" stop-color="#f1f3f5"/>
        <stop offset="1" stop-color="#cfd5db"/>
      </linearGradient>
      <filter id="bevel" x="-5%" y="-10%" width="110%" height="125%">
        <feDropShadow dx="1.5" dy="2.5" stdDeviation="1.5" flood-color="#3c444e" flood-opacity="0.8"/>
      </filter>
    </defs>

    <g class="back-title" filter="url(#bevel)">
      <text class="title-text" x="170" y="145" font-size="92" textLength="240" lengthAdjust="spacingAndGlyphs">THE</text>
      <text class="title-text" x="60" y="235" font-size="96" textLength="458" lengthAdjust="spacingAndGlyphs">ASHWARD</text>
    </g>

    <g class="back-blurb">
      <text class="blurb-line" x="289" y="281" textLength="203" lengthAdjust="spacingAndGlyphs">Every dream is a nightmare in waiting.</text>
      <text class="blurb-line" x="289" y="306" textLength="460" lengthAdjust="spacingAndGlyphs">Fourteen-year-old Callie has a secret. One she doesn’t share with anyone, including her</text>
      <text class="blurb-line" x="289" y="331" textLength="446" lengthAdjust="spacingAndGlyphs">best friend and twin brother, Luca. Sometimes, in her sleep, she visits a breathtaking</text>
      <text class="blurb-line" x="289" y="356" textLength="423" lengthAdjust="spacingAndGlyphs">place that is all hers, until tonight. On this visit, her brother is there, but so is the</text>
      <text class="blurb-line" x="289" y="381" textLength="357" lengthAdjust="spacingAndGlyphs">monster Callie greatly fears and who attacks and carries Luca away.</text>
      <text class="blurb-line" x="289" y="406" textLength="436" lengthAdjust="spacingAndGlyphs">During those same moments, Callie’s grandfather awakens from his nightmare of a</text>
      <text class="blurb-line" x="289" y="431" textLength="455" lengthAdjust="spacingAndGlyphs">long-forgotten place to learn that his grandson is missing. When Callie confides in him</text>
      <text class="blurb-line" x="289" y="456" textLength="462" lengthAdjust="spacingAndGlyphs">about her dream, it triggers a landslide of lost memories. Memories of a night fifty years</text>
      <text class="blurb-line" x="289" y="481" textLength="279" lengthAdjust="spacingAndGlyphs">earlier, when his cousin disappeared without a trace.</text>
      <text class="blurb-line" x="289" y="506" textLength="459" lengthAdjust="spacingAndGlyphs">Callie and her grandfather soon discover they share a link to a perilous place where the</text>
      <text class="blurb-line" x="289" y="531" textLength="457" lengthAdjust="spacingAndGlyphs">thresholds of infinite worlds touch, myths turn into reality, wonder and death are close</text>
      <text class="blurb-line" x="289" y="556" textLength="292" lengthAdjust="spacingAndGlyphs">companions, and friendships are forged and destroyed.</text>
      <text class="blurb-line" x="289" y="581" textLength="453" lengthAdjust="spacingAndGlyphs">Can Callie, her grandfather, and his three lifelong friends, uncover this world’s secrets</text>
      <text class="blurb-line" x="289" y="606" textLength="454" lengthAdjust="spacingAndGlyphs">and rescue those they lost before carnage comes into their lives? Or will they discover</text>
      <text class="blurb-line" x="289" y="631" textLength="402" lengthAdjust="spacingAndGlyphs">there is no longer any escape for anyone from this place called The Ashward?</text>
    </g>

    <g class="spine">
      <g transform="translate(581 40) rotate(90)">
        <text class="spine-title" x="0" y="0" font-size="42" textLength="373" lengthAdjust="spacingAndGlyphs">THE ASHWARD</text>
      </g>
      <g transform="translate(588 458) rotate(90)">
        <text class="author-text" x="0" y="0" font-size="32" textLength="312" lengthAdjust="spacing">Elliot Varden</text>
      </g>
    </g>

    <g class="front-title" filter="url(#bevel)">
      <text class="title-text" x="790" y="145" font-size="92" textLength="240" lengthAdjust="spacingAndGlyphs">THE</text>
      <text class="title-text" x="681" y="235" font-size="96" textLength="458" lengthAdjust="spacingAndGlyphs">ASHWARD</text>
    </g>

    <text class="subtitle-text" x="793" y="282" textLength="193" lengthAdjust="spacingAndGlyphs">Book 1: Marcus</text>

    <text class="author-text" x="717" y="810" font-size="40" textLength="390" lengthAdjust="spacing">Elliot Varden</text>
  </svg>

  <div class="barcode-area"></div>
</div>
</body>
</html>
```